BOLD & MINIMALIST DESIGN NEEDED

We want a very bold but minimalistic business card design that is impactful and utilizes both sides of the business card. Our current logo is included for your use.

We want bold fonts and good use of negative space. We don't want the logo to overpower the design.

Target Market(s)

Professionals who are building new commercial buildings.

Industry/Entity Type

Construction

Contact Information for Business Card

Name, Title, email, office phone, cell phone, website

Font styles to use
Serif
Sans Serif

Requirements
Must have
• Bold design!

```html
<!DOCTYPE html>
<html lang="en">
<head>
<meta charset="utf-8">
<title>Ridgeline Design + Build — Business Card</title>
<link rel="stylesheet" href="https://fonts.googleapis.com/css2?family=Montserrat:wght@400;500;800;900&display=swap">
<style>
  :root {
    --bg-dark: #2e2e2e;
    --bg-light: #5a5a5a;
    --card-black: #121212;
    --card-white: #f4f4f2;
    --accent-green: #5fae1f;
    --ink: #111111;
    --ink-soft: #2a2a2a;
    --ghost: #e4e4e2;
    --rule: #cfcfcc;
  }
  * { box-sizing: border-box; margin: 0; padding: 0; }
  html, body { width: 1200px; height: 1050px; overflow: hidden; }
  body {
    background: linear-gradient(135deg, var(--bg-dark) 0%, var(--bg-light) 100%);
    font-family: "Montserrat", sans-serif;
    position: relative;
  }
  .card {
    position: absolute;
    left: 280px;
    width: 640px;
    height: 366px;
    border-bottom: 8px solid var(--accent-green);
    box-shadow: 0 24px 50px rgba(0,0,0,0.45);
    overflow: hidden;
  }
  /* Back side */
  .card-back {
    top: 100px;
    background: var(--card-black);
    display: flex;
    align-items: center;
    justify-content: center;
  }
  .brand {
    display: flex;
    align-items: center;
    gap: 16px;
  }
  .brand-square {
    width: 34px;
    height: 34px;
    background: var(--accent-green);
  }
  .brand-name {
    color: #ffffff;
    font-weight: 900;
    font-size: 40px;
    letter-spacing: 1px;
    text-transform: uppercase;
    line-height: 1;
  }
  .brand-name small {
    display: block;
    font-size: 40px;
  }
  /* Front side */
  .card-front {
    top: 570px;
    background: var(--card-white);
  }
  .ghost-name {
    position: absolute;
    left: 18px;
    bottom: -18px;
    font-weight: 900;
    font-size: 92px;
    color: var(--ghost);
    letter-spacing: 2px;
    text-transform: uppercase;
    white-space: nowrap;
  }
  .identity {
    position: absolute;
    right: 380px;
    top: 118px;
    text-align: right;
  }
  .person-name {
    font-weight: 900;
    font-size: 30px;
    color: var(--ink);
    letter-spacing: 0.5px;
    text-transform: uppercase;
    white-space: nowrap;
  }
  .person-title {
    font-weight: 500;
    font-size: 16px;
    color: var(--ink-soft);
    margin-top: 2px;
  }
  .divider {
    position: absolute;
    left: 282px;
    top: 110px;
    width: 1px;
    height: 150px;
    background: var(--rule);
  }
  .contact {
    position: absolute;
    left: 306px;
    top: 112px;
    list-style: none;
    font-size: 15px;
    font-weight: 500;
    color: var(--ink-soft);
    line-height: 1.55;
  }
  .contact li { display: flex; align-items: center; gap: 8px; }
  .contact .address { padding-left: 20px; }
  .icon { width: 12px; height: 12px; flex: none; }
</style>
</head>
<body>
  <section class="card card-back" aria-label="Card back">
    <div class="brand">
      <span class="brand-square"></span>
      <span class="brand-name">Ridgeline<small>Design + Build</small></span>
    </div>
  </section>

  <section class="card card-front" aria-label="Card front">
    <div class="ghost-name" aria-hidden="true">Ridgeline</div>
    <div class="identity">
      <p class="person-name">Marek Vogel</p>
      <p class="person-title">Director</p>
    </div>
    <div class="divider"></div>
    <ul class="contact">
      <li class="address">Lindenweg 14,</li>
      <li class="address">30159 Hannover</li>
      <li>
        <svg class="icon" viewBox="0 0 12 12"><path d="M2.5 1 L4.5 1 L5.3 3.6 L4 4.6 C4.7 6 5.9 7.3 7.4 8 L8.4 6.7 L11 7.5 L11 9.5 C11 10.4 10.2 11 9.3 11 C4.8 10.6 1.4 7.2 1 2.7 C1 1.8 1.6 1 2.5 1 Z" fill="var(--accent-green)"/></svg>
        0160 5550142
      </li>
      <li>
        <svg class="icon" viewBox="0 0 12 12"><rect x="0.5" y="2" width="11" height="8" fill="var(--accent-green)"/><path d="M0.5 2 L6 6.5 L11.5 2" fill="none" stroke="#ffffff" stroke-width="1"/></svg>
        info@ridgeline-build.com
      </li>
      <li>
        <svg class="icon" viewBox="0 0 12 12"><circle cx="6" cy="6" r="5" fill="none" stroke="var(--accent-green)" stroke-width="1.3"/><ellipse cx="6" cy="6" rx="2.2" ry="5" fill="none" stroke="var(--accent-green)" stroke-width="1"/><line x1="1" y1="6" x2="11" y2="6" stroke="var(--accent-green)" stroke-width="1"/></svg>
        www.ridgeline-build.com
      </li>
    </ul>
  </section>
</body>
</html>
```